Orthobiologic, StemCell, Bone Marrow Aspirate Device Distributor

We need a wordpress fully functioning website design for an innovative ortho-biologic, Bone Marrow Aspirate Device that extracts stem cells for orthopedic regenerative medical professionals. We also offer state of the art training in there office setting with licensed medical staff, a full service support team, and software for tracking patient outcome over time. We are an innovative company that prides itself on gold standard support. We will have other offerings on our website and would like a spot for "future" products. We would like to see designs that look professional, medical, and convey support, security, science, and innovation. We prefer shades of blue and red/orange. I particularly like the following websites that also sell the same device in order of preference:regenacelltherapy.comhttps://aspire-medical.eu/marrow-cellution/https://www.matrixbiosurgical.com/#emerging-solutions-in-healthcareElite2elite.comI have attached a few pictures of the device for reference

Target Market(s)

Orthopedics, Regenerative medicine doctors, Industry representatives, Hospitals

Industry/Entity Type

Medical Equipment

Coding

Coded - Design and coding required

Colors
3176b5
33a6d7
f37022
ec1f27

Requirements
Must have
• It must be able to have videos which I can supply, email, online ordering, and sfax. I have a domain name Coralweavesolutions.com . It must have a FAQ section which you can obtain some information from https://www.tolvenclinical.com/solutions#resources
• The device is manufactured by Dulmor and this is the link to the product page http://www.dulmor.com/quintadraw
• I am currently working on a custom logo and should be able to supply that in short order. I prefer shades of blue and red.
Nice to have
• I would love to have a graphic video as seen here: please see quinta draw vs bone marrow aspirate concentrate.
• https://www.tolvenclinical.com/solutions#competition
• I would pay considerably more to have something similar if it is at all possible
Should not have
• Nothing specific

```html
<!DOCTYPE html>
<html lang="en">
<head>
<meta charset="utf-8">
<title>Coralweavesolutions</title>
<link href="https://fonts.googleapis.com/css2?family=Lato:wght@400;700&family=Poppins:wght@400;500;600;700&family=Montserrat:wght@400;500;600&display=swap" rel="stylesheet">
<style>
:root{
  --blue:#1a7ff0;
  --blue-deep:#3176b5;
  --sky:#33a6d7;
  --orange:#f37022;
  --red:#ec1f27;
  --ink:#222;
  --heading:#3a3a3a;
  --muted:#6d6d6d;
  --gray-band:#ebebeb;
  --footer:#1c2331;
  --star:#f6c400;
}
*{box-sizing:border-box;margin:0;padding:0}
html,body{width:1200px;height:3867px;overflow:hidden;background:#fff}
body{position:relative;font-family:"Lato",sans-serif;color:var(--ink)}
.abs{position:absolute}

/* header */
.brand{left:150px;top:12px;display:flex;align-items:center;gap:10px}
.brand-mark{width:66px;height:66px;border-radius:50%;background:var(--sky)}
.brand-name{font-family:"Lato",sans-serif;font-size:13px;color:var(--blue-deep);font-weight:400}
.call{left:766px;top:24px;display:flex;align-items:center;gap:12px}
.call-icon{width:36px;height:36px;border-radius:50%;background:var(--blue-deep);display:flex;align-items:center;justify-content:center}
.call small{display:block;font-size:12px;color:#444}
.call strong{font-size:17px;font-weight:400;color:#111}
.quote-btn{left:951px;top:26px;width:129px;height:38px;background:var(--blue-deep);color:#fff;font-size:11px;font-weight:700;display:flex;align-items:center;justify-content:center;box-shadow:0 2px 4px rgba(0,0,0,.3)}
.nav{top:101px;left:0;width:1200px}
.nav a{position:absolute;font-size:19px;color:#222;text-decoration:none;font-weight:500}
.nav .active::after{content:"";position:absolute;left:0;right:-8px;top:29px;height:4px;background:var(--blue-deep)}

/* hero */
.hero{top:153px;left:0;width:1200px;height:553px;background:radial-gradient(circle at 40% 40%,#4a5d7a 0,#1d2a44 45%,#0b1224 100%)}
.hero-title{width:1200px;text-align:center;font-family:"Poppins",sans-serif;font-weight:700;color:#fff}
.hero-arrow{width:34px;height:34px;border-radius:50%;background:#fff;display:flex;align-items:center;justify-content:center}
.cta-white{left:498px;top:506px;width:185px;height:67px;background:#fff;font-family:"Poppins",sans-serif;font-weight:600;font-size:21px;display:flex;align-items:center;justify-content:center;color:#111}

/* who we are */
.who-block{left:0;top:770px;width:261px;height:397px;background:var(--blue)}
.who-photo{left:23px;top:821px;width:439px;height:296px;background:radial-gradient(circle at 55% 45%,#2c5fb0 0,#12306b 40%,#000 75%)}
.section-h{font-family:"Poppins",sans-serif;font-weight:700;font-size:38px;color:var(--heading);letter-spacing:1px}
.section-h em{font-style:normal;color:var(--blue)}
.who-text{left:549px;top:852px;width:508px;font-family:"Montserrat",sans-serif;font-size:14px;line-height:29px;color:var(--muted);text-align:justify}
.btn-blue{background:var(--blue);color:#fff;display:flex;align-items:center;justify-content:center;font-weight:700}

/* video */
.video-band{left:0;top:1230px;width:1200px;height:412px;background:radial-gradient(circle at 55% 55%,#2e8de0 0,#1360b8 45%,#082a5a 100%)}
.video-line{width:1200px;text-align:center;font-family:"Montserrat",sans-serif;font-size:33px;color:#fff}

/* products */
.card{width:244px;height:283px;background:#fff;box-shadow:0 3px 8px rgba(0,0,0,.25)}
.card .pic{position:absolute;left:12px;top:12px;right:12px;height:190px;background:linear-gradient(180deg,#fafafa,#eeeeee)}
.card .label{position:absolute;left:0;right:0;bottom:0;height:63px;background:var(--blue-deep);color:#fff;font-family:"Poppins",sans-serif;font-weight:600;font-size:18px;display:flex;align-items:center;justify-content:center;text-align:center;line-height:21px;letter-spacing:.5px}

/* testimonials */
.testi-band{left:0;top:2328px;width:1200px;height:478px;background:var(--gray-band)}
.tcard{width:308px;height:203px;background:#fff;box-shadow:0 1px 4px rgba(0,0,0,.2)}
.tcard .avatar{position:absolute;left:6px;top:52px;width:95px;height:95px;border-radius:50%;background:linear-gradient(135deg,#c99a80,#6c4a3a)}
.tcard .place{position:absolute;left:120px;width:175px;top:24px;text-align:center;font-weight:700;font-size:15px}
.tcard .stars{position:absolute;left:120px;width:175px;top:50px;text-align:center;color:var(--star);font-size:17px;letter-spacing:1px}
.tcard .quote{position:absolute;left:120px;width:175px;top:80px;text-align:center;font-style:italic;font-size:13px;line-height:26px;color:#8a8a8a}
.tcard .who{position:absolute;left:120px;width:175px;top:160px;text-align:center;font-size:15px;color:#333}
.dot{width:16px;height:16px;border-radius:50%;background:var(--orange)}

/* faq */
.faq-item{left:131px;width:952px;border:2px solid #d4d4d4;font-family:"Montserrat",sans-serif;font-size:18px;letter-spacing:1.5px;color:#222}
.faq-item .q{position:absolute;left:59px;top:18px}
.faq-item .sign{position:absolute;right:28px;top:14px;color:var(--blue);font-size:26px}

/* footer */
.footer{left:0;top:3488px;width:1200px;height:379px;background:var(--footer);font-family:"Montserrat",sans-serif}
.fh{font-family:"Poppins",sans-serif;font-size:18px;color:#fff;font-weight:500}
.fsmall{font-size:13px;color:#7d8594}
.social{width:18px;height:18px;background:#fff;border-radius:3px}
</style>
</head>
<body>

<header>
  <div class="abs brand"><span class="brand-mark"></span><span class="brand-name">CORALWEAVESOLUTIONS</span></div>
  <div class="abs call">
    <span class="call-icon"><svg width="18" height="18" viewBox="0 0 24 24"><path fill="#fff" d="M6.6 10.8a15.1 15.1 0 0 0 6.6 6.6l2.2-2.2a1 1 0 0 1 1-.25 11.4 11.4 0 0 0 3.6.57 1 1 0 0 1 1 1V20a1 1 0 0 1-1 1A17 17 0 0 1 3 4a1 1 0 0 1 1-1h3.5a1 1 0 0 1 1 1c0 1.25.2 2.45.57 3.57a1 1 0 0 1-.25 1z"/></svg></span>
    <span><small>Call Us Today</small><strong>555-014-2290</strong></span>
  </div>
  <div class="abs quote-btn">REQUEST A QUOTE</div>
  <nav class="abs nav">
    <a class="active" style="left:150px">Home</a>
    <a style="left:265px">Products</a>
    <a style="left:409px">Providers</a>
    <a style="left:559px">Resources</a>
    <a style="left:715px">Distributors</a>
    <a style="left:888px">Faq</a>
    <a style="left:985px">Contact Us</a>
  </nav>
</header>

<section class="abs hero" role="img" aria-label="Microscope view of red and translucent blood cells">
  <div class="abs hero-title" style="top:180px;font-size:50px">WELOME TO</div>
  <div class="abs hero-title" style="top:258px;font-size:50px">Coralweavesolutions</div>
  <div class="abs hero-arrow" style="left:133px;top:279px"><svg width="18" height="18" viewBox="0 0 24 24"><path d="M20 12H5M11 5l-7 7 7 7" stroke="#222" stroke-width="2" fill="none"/></svg></div>
  <div class="abs hero-arrow" style="left:1050px;top:279px"><svg width="18" height="18" viewBox="0 0 24 24"><path d="M4 12h15M13 5l7 7-7 7" stroke="#222" stroke-width="2" fill="none"/></svg></div>
</section>
<div class="abs cta-white">GET STARTED</div>

<section>
  <div class="abs who-block"></div>
  <div class="abs who-photo" role="img" aria-label="Blue stem cells under a microscope"></div>
  <h2 class="abs section-h" style="left:549px;top:790px">WHO <em>WE ARE</em></h2>
  <p class="abs who-text">Lorem ipsum dolor sit amet, consectetur adipiscing elit, sed do eiusmod tempor incididunt ut labore et dolore magna aliqua. Quis ipsum suspendisse ultrices gravida. Risus commodo viverra maecenas accumsan lacus vel facilisis. Lorem ipsum dolor sit amet, consectetur adipiscing elit, sed do eiusmod tempor incididunt ut labore et dolore magna aliqua. Quis ipsum suspendisse ultrices gravida. Risus commodo viverra maecenas accumsan lacus vel facilisis.</p>
  <div class="abs btn-blue" style="left:549px;top:1091px;width:147px;height:51px;font-size:14px">READ MORE</div>
</section>

<section class="abs video-band" role="img" aria-label="Close-up of blue cells behind a video message">
  <div class="abs video-line" style="top:100px;left:38px">Lorem ipsum dolor sit amet, consectetur adipiscing elit,</div>
  <div class="abs video-line" style="top:168px;left:38px">sed do eiusmod tempor incididunti</div>
  <svg class="abs" style="left:585px;top:243px" width="70" height="70" viewBox="0 0 70 70"><circle cx="35" cy="35" r="32" fill="none" stroke="#fff" stroke-width="2.5"/><path d="M28 22v26l20-13z" fill="none" stroke="#fff" stroke-width="2.5"/></svg>
</section>

<section>
  <h2 class="abs section-h" style="left:0;width:1232px;text-align:center;top:1718px">FUTURE PRODUCTS</h2>
  <div class="abs card" style="left:82px;top:1860px"><div class="pic" role="img" aria-label="Aspiration needle set with green handle"></div><div class="label">VITAL SIGN MONITOR</div></div>
  <div class="abs card" style="left:356px;top:1860px"><div class="pic" role="img" aria-label="Purple aspiration device"></div><div class="label">QUINTA DRAW</div></div>
  <div class="abs card" style="left:630px;top:1860px"><div class="pic" role="img" aria-label="Bone marrow needle with green handle"></div><div class="label">BONE MARROW</div></div>
  <div class="abs card" style="left:904px;top:1860px"><div class="pic" role="img" aria-label="Curved infusion cannula"></div><div class="label">GALACTOGRAPHY<br>INFUSION UNITS</div></div>
  <div class="abs btn-blue" style="left:527px;top:2215px;width:160px;height:54px;font-family:'Poppins',sans-serif;font-size:21px;font-weight:600">View More</div>
</section>

<section class="abs testi-band">
  <h2 class="abs section-h" style="left:0;width:1200px;text-align:center;top:44px">TESTIMONIAL</h2>
  <div class="abs tcard" style="left:109px;top:169px"><div class="avatar" role="img" aria-label="Client portrait"></div><div class="place">Holland Canals</div><div class="stars">★★★★★</div><div class="quote">Lorem ipsum dolor sit amet, consecteturlacus</div><div class="who">Nora Quill</div></div>
  <div class="abs tcard" style="left:446px;top:169px"><div class="avatar" role="img" aria-label="Client portrait"></div><div class="place">Temple Tour</div><div class="stars">★★★★★</div><div class="quote">Lorem ipsum dolor sit amet, consecteturlacus</div><div class="who">Ezra Vale</div></div>
  <div class="abs tcard" style="left:778px;top:169px"><div class="avatar" role="img" aria-label="Client portrait"></div><div class="place">Barcelona</div><div class="stars">★★★★★</div><div class="quote">Lorem ipsum dolor sit amet, consecteturlacus</div><div class="who">Milo Brandt</div></div>
  <div class="abs dot" style="left:566px;top:430px;background:none;border:2px solid var(--orange)"></div>
  <div class="abs dot" style="left:592px;top:430px"></div>
  <div class="abs dot" style="left:616px;top:430px"></div>
</section>

<section>
  <h2 class="abs" style="left:0;width:1222px;text-align:center;top:2868px;font-family:'Poppins',sans-serif;font-size:34px;font-weight:700;color:#111">FAQ</h2>
  <div class="abs faq-item" style="top:2954px;height:58px"><span class="q">What should the customer know about your pricing</span><span class="sign">+</span></div>
  <div class="abs faq-item" style="top:3025px;height:58px"><span class="q">What is your typical process for working with a new customer?</span><span class="sign">+</span></div>
  <div class="abs faq-item" style="top:3095px;height:58px"><span class="q">What education and/or training do you have that relates to your work?</span><span class="sign">+</span></div>
  <div class="abs faq-item" style="top:3167px;height:98px"><span class="q">How did you get started doing this type of work?</span><span class="sign">-</span><span class="q" style="top:58px;color:#555">We all are different</span></div>
  <div class="abs faq-item" style="top:3290px;height:58px"><span class="q">What types of customers have you worked with?</span><span class="sign">+</span></div>
  <div class="abs faq-item" style="top:3362px;height:58px"><span class="q" style="top:8px;line-height:22px">What advice would you give a customer looking to<br>hire a provider in your area of work?</span><span class="sign">+</span></div>
</section>

<footer class="abs footer">
  <div class="abs" style="left:152px;top:85px;width:110px;height:110px;border-radius:50%;background:var(--sky)"></div>
  <p class="abs" style="left:120px;width:190px;top:220px;text-align:center;color:#fff;font-style:italic;font-size:13px;line-height:26px;font-family:'Lato',sans-serif">Lorem ipsum dolor sit amet, consecteturlacus</p>

  <div class="abs fh" style="left:397px;top:80px">Contact Information</div>
  <svg class="abs" style="left:400px;top:123px" width="18" height="18" viewBox="0 0 24 24"><path d="M22 2 2 11l7 3 2 8 4-6 5 4z" fill="#fff"/></svg>
  <div class="abs fsmall" style="left:426px;top:124px">Harbor Point, Lanford, 2nd block</div>
  <div class="abs fsmall" style="left:426px;top:157px">4417 Tower no 5, floor 2</div>
  <svg class="abs" style="left:402px;top:204px" width="15" height="12" viewBox="0 0 24 18"><rect width="24" height="18" fill="#fff"/><path d="M0 0l12 9 12-9" stroke="#1c2331" stroke-width="2" fill="none"/></svg>
  <div class="abs fsmall" style="left:426px;top:202px"><span style="color:#fff">Email:</span> info@coralweavesolutions.com</div>
  <svg class="abs" style="left:402px;top:234px" width="15" height="15" viewBox="0 0 24 24"><path fill="#fff" d="M6.6 10.8a15.1 15.1 0 0 0 6.6 6.6l2.2-2.2a1 1 0 0 1 1-.25 11.4 11.4 0 0 0 3.6.57 1 1 0 0 1 1 1V20a1 1 0 0 1-1 1A17 17 0 0 1 3 4a1 1 0 0 1 1-1h3.5a1 1 0 0 1 1 1c0 1.25.2 2.45.57 3.57a1 1 0 0 1-.25 1z"/></svg>
  <div class="abs fsmall" style="left:426px;top:233px"><span style="color:#fff">Phone:</span> 555 014 2291</div>

  <div class="abs fh" style="left:771px;top:80px">Newsletter</div>
  <div class="abs fsmall" style="left:771px;top:124px">Enter your email &amp; subcribing newsletter</div>
  <div class="abs" style="left:771px;top:160px;width:211px;height:40px;background:#2a3243;display:flex;align-items:center;gap:10px;padding-left:16px;color:#fff;font-size:12px">
    <svg width="15" height="11" viewBox="0 0 24 18"><rect x="1" y="1" width="22" height="16" fill="none" stroke="var(--orange)" stroke-width="2"/><path d="M1 1l11 8 11-8" stroke="var(--orange)" stroke-width="2" fill="none"/></svg>Email address
  </div>
  <div class="abs" style="left:982px;top:160px;width:106px;height:40px;background:var(--orange);color:#fff;font-size:11px;font-weight:600;display:flex;align-items:center;justify-content:center">SUBSCRIBE</div>
  <div class="abs social" style="left:777px;top:243px"></div>
  <div class="abs social" style="left:826px;top:243px"></div>
  <div class="abs social" style="left:879px;top:243px"></div>
  <div class="abs social" style="left:930px;top:243px"></div>
  <div class="abs social" style="left:977px;top:243px"></div>

  <div class="abs" style="left:86px;top:324px;width:1028px;height:1px;background:#2f3749"></div>
  <div class="abs fsmall" style="left:0;width:1178px;text-align:center;top:347px;font-size:12px">2019 ©  Copyrights. All rights reserved</div>
</footer>

</body>
</html>
```